Redesign of the UI of a customer service platform

To improve the user experience of our customers, we need a new design for our agent interface of our customer service platform (velorant.com).
The focus will be on the dashboard and the inbox screens (see attached) along with the common UI elements (Buttons, menu, fonts, forms...)
We want a simple and distinctive design

Target Market(s)

Worldwide

Industry/Entity Type

It Service

Number of Pages Required

3 page

Font styles to use
Sans Serif

Requirements
Must have
• New Onboarding page: this is a new page that is shown to user the first time they login to the platform. This will replace the current onboarding screen (setup SMS, Setup widget...etc)
• Dashboard page: to access important information and activate services (see screenshot from current site)
• Inbox page: to manage all the interactions with customers. (see screenshot from current site)
• UI elements (buttons, menus, forms, tables, fonts, color palette)

```html
<!DOCTYPE html>
<html lang="en">
<head>
<meta charset="utf-8">
<title>Velorant – Inbox</title>
<link href="https://fonts.googleapis.com/css2?family=Open+Sans:ital,wght@0,400;0,600;0,700;1,400&display=swap" rel="stylesheet">
<style>
:root{
  --topbar:#1d1d1d;
  --sidebar:#2f2f2f;
  --burger:#3a3a3a;
  --cyan:#2ab4e9;
  --orange:#ee5f2c;
  --blue:#1466b8;
  --red:#e8413a;
  --page:#efefef;
  --white:#ffffff;
  --line:#e3e3e3;
  --text:#333333;
  --muted:#8a8a8a;
  --photo:#e9c9a6;
  --icon-grey:#9b9b9b;
  --green:#2bd12b;
}
*{box-sizing:border-box;margin:0;padding:0}
html,body{width:1200px;height:667px;overflow:hidden}
body{font-family:"Open Sans",Arial,sans-serif;background:var(--page);color:var(--text);position:relative;font-size:10px}
.abs{position:absolute}
svg.ic{display:inline-block;flex:none;fill:currentColor}
.defs{position:absolute;width:0;height:0;overflow:hidden}

/* top bar */
.topbar{left:0;top:0;width:1200px;height:38px;background:var(--topbar);color:#ddd}
.brand{left:29px;top:5px;display:flex;align-items:center;gap:6px;color:#fff;font-weight:700;font-size:19px;letter-spacing:-.2px;line-height:26px}
.brand-dot{width:15px;height:15px;border-radius:50%;border:3px solid #fff}
.burger{left:170px;top:0;width:50px;height:38px;background:var(--burger);display:flex;align-items:center;justify-content:center}
.top-item{top:0;height:38px;display:flex;align-items:center;gap:5px;font-size:10px;font-weight:600;color:#ccc}
.notify .count{position:absolute;top:9px;left:9px;background:var(--cyan);color:#fff;border-radius:50%;width:10px;height:10px;font-size:7px;text-align:center;line-height:10px;font-weight:700}
.status-dot{width:7px;height:7px;border-radius:50%;background:var(--green)}

/* sidebar */
.sidebar{left:0;top:38px;width:170px;height:629px;background:var(--sidebar)}
.nav{position:absolute;left:0;top:16px;width:170px;list-style:none}
.nav li{height:33.4px;display:flex;align-items:center;padding-left:28px;gap:9px;color:#e6e6e6;font-size:8.5px;font-weight:700;letter-spacing:.2px;position:relative}
.nav li.active{background:var(--cyan);color:#fff}
.nav .pill{position:absolute;right:11px;top:10px;background:#fff;color:var(--cyan);border-radius:50%;width:13px;height:13px;font-size:8px;text-align:center;line-height:13px}
.nav .chev{position:absolute;right:20px;top:12px}
.feedback{left:40px;top:638px;color:#999;font-size:9.5px;display:flex;gap:8px;align-items:center}

/* page */
.page-title{left:193px;top:54px;font-size:15px;font-weight:400;display:flex;gap:8px;align-items:center;color:#333}
.profile{left:1113px;top:54px;width:21px;height:21px;border-radius:50%;background:#c8c8c8;display:flex;align-items:center;justify-content:center;color:#fff}
.tabs{left:193px;top:81px;display:flex}
.tab{height:35px;display:flex;align-items:center;justify-content:center;font-size:11.5px;color:#333}
.tab.active{background:var(--white);border-top:3px solid var(--red);width:78px}
.tab.dept{width:100px}
.tab.acct{width:86px}
.tab sup{background:var(--red);color:#fff;border-radius:50%;width:10px;height:10px;font-size:7px;line-height:10px;text-align:center;display:inline-block;vertical-align:7px}
.panel{left:193px;top:116px;width:950px;height:511px;background:var(--white)}

/* chat list */
.chat-list{left:210px;top:137px;width:249px;background:#f4f4f4}
.chat{height:46.5px;display:flex;align-items:center;padding:0 6px 0 13px;gap:11px;border-bottom:1px solid var(--line);font-size:8.5px}
.chat.active{height:41px;background:var(--cyan);color:#fff;border-left:5px solid var(--orange);padding-left:8px;border-bottom:none}
.chat .av{width:29px;height:29px;border-radius:50%;background:#fff;display:flex;align-items:center;justify-content:center;flex:none;color:var(--icon-grey)}
.chat.active .av{background:var(--photo)}
.chat .num{font-weight:700;line-height:1.1;width:20px;font-size:8px}
.chat .name{font-weight:700;flex:1;font-size:8.8px}
.chat .time{color:#555;display:flex;gap:5px;align-items:center;font-size:8.8px}
.chat .time svg{color:#999}
.chat.active .time,.chat.active .time svg{color:#fff}
.done{left:210px;top:336px;width:249px;text-align:center;font-size:8px;line-height:12px}
.done b{color:var(--red);display:block}
.done span{color:var(--muted)}

/* conversation */
.conv-head{left:480px;top:143px;width:645px;height:20px;display:flex;align-items:center;font-size:12.5px;font-weight:700;color:#444}
.red-dot{width:6px;height:6px;border-radius:50%;background:var(--red);margin:0 18px 0 0}
.actions{position:absolute;right:0;top:0;display:flex;gap:5px}
.btn{height:20px;padding:0 8px;color:#fff;font-size:9px;display:flex;align-items:center;gap:4px;font-weight:600}
.btn.close{background:var(--cyan)}.btn.transfer{background:var(--orange)}.btn.ban{background:var(--blue)}
.orange-bar{left:480px;top:175px;width:645px;height:26px;background:var(--orange);color:#fff;font-size:9px;font-weight:600;display:flex;align-items:center;justify-content:space-between;padding:0 14px 0 8px}
.orange-bar span{display:flex;align-items:center;gap:5px}
.messages{left:480px;top:201px;width:645px;height:205px;background:#f9f9f9;border:1px solid var(--line);border-top:none}
.msg-av{width:29px;height:29px;border-radius:50%;background:var(--photo)}
.msg-in{left:9px;top:13px;display:flex;align-items:center;gap:12px;font-size:9px;font-weight:700}
.msg-out{right:14px;top:54px;display:flex;align-items:center;gap:12px;font-size:9px;text-align:right;line-height:12px}
.msg-out b{color:var(--blue)}.msg-out em{font-style:normal;color:#c0392b;display:block}
.composer{left:10px;top:168px;width:624px;height:26px;background:#fff;border:1px solid var(--line);font-size:9px;color:#888;display:flex;align-items:center;justify-content:space-between;padding:0 8px 0 11px}
.composer svg{color:#777}

/* details */
.details{left:480px;top:424px;width:645px;height:140px;border:1px solid var(--line);background:#fafafa}
.dtabs{display:flex;height:34px;background:#fff;border-bottom:1px solid var(--line);position:relative}
.dtab{padding:0 15px;display:flex;align-items:center;gap:5px;font-size:10.5px;color:#333}
.dtab.active{border-top:2px solid var(--red);border-right:1px solid var(--line);background:#fafafa;margin-bottom:-1px}
.minus{position:absolute;right:12px;top:16px;width:9px;height:2px;background:#444}
.fields{position:absolute;left:18px;top:79px;width:616px;display:flex;align-items:center;justify-content:space-between;font-size:9.5px;font-style:italic}
.fields span{display:flex;align-items:center;gap:5px}
.f-name{color:var(--orange);font-style:normal;font-size:10.5px}
.f-email{color:var(--cyan)}.f-phone{color:var(--blue)}.f-addr{color:#c0392b}.f-city{color:#e49b1c}.f-country{color:#1d4f8f}
.btn.edit{background:var(--orange);font-style:normal;font-size:10px;font-weight:400}

.footer-stats{left:917px;top:639px;display:flex;gap:14px;color:#888;font-size:9px}
.zoom{left:1172px;top:638px;color:var(--blue);font-size:9px;font-weight:700}
</style>
</head>
<body>

<svg class="defs" aria-hidden="true">
  <symbol id="i-gauge" viewBox="0 0 12 12"><path d="M6 2a6 6 0 016 6v2H0V8a6 6 0 016-6zm0 3.5L4.5 8.5h3z"/></symbol>
  <symbol id="i-tray" viewBox="0 0 12 12"><path d="M2 2h8l2 5v4H0V7zm0.5 5H4l1 1.5h2L8 7h1.5L8.6 3.2H3.4z" fill-rule="evenodd"/></symbol>
  <symbol id="i-tag" viewBox="0 0 12 12"><path d="M6.5 0H12v5.5L5.5 12 0 6.5zM9.5 1.7a.8.8 0 100 1.6.8.8 0 000-1.6z" fill-rule="evenodd"/></symbol>
  <symbol id="i-users" viewBox="0 0 12 12"><circle cx="4" cy="4" r="2.2"/><circle cx="8.5" cy="3.5" r="1.8"/><path d="M0 11a4 3.5 0 018 0zM7 7.5a3.5 3 0 015 2.5H8.5z"/></symbol>
  <symbol id="i-bars" viewBox="0 0 12 12"><path d="M0 11h12v1H0zM1 6h2v5H1zM4.5 3h2v8h-2zM8 7h2v4H8z"/></symbol>
  <symbol id="i-gear" viewBox="0 0 12 12"><path d="M5 0h2l.4 1.8 1.6.7 1.6-1 1.4 1.4-1 1.6.7 1.6L12 5v2l-1.8.4-.7 1.6 1 1.6-1.4 1.4-1.6-1-1.6.7L7 12H5l-.4-1.8-1.6-.7-1.6 1L0 9.1l1-1.6L.4 6 0 5V7zm1 4a2 2 0 100 4 2 2 0 000-4z" fill-rule="evenodd"/></symbol>
  <symbol id="i-user" viewBox="0 0 12 12"><circle cx="6" cy="3.5" r="3"/><path d="M0 12a6 5 0 0112 0z"/></symbol>
  <symbol id="i-chat" viewBox="0 0 12 12"><path d="M6 1c3.3 0 6 2 6 4.5S9.3 10 6 10c-.6 0-1.2-.1-1.7-.2L1 11.5l1-2.6C.8 8 0 6.8 0 5.5 0 3 2.7 1 6 1z"/></symbol>
  <symbol id="i-mail" viewBox="0 0 12 12"><path d="M0 2h12v1.2L6 7 0 3.2zM0 4.6l6 3.8 6-3.8V10H0z"/></symbol>
  <symbol id="i-phone" viewBox="0 0 12 12"><path d="M1 0h10a1 1 0 011 1v10a1 1 0 01-1 1H1a1 1 0 01-1-1V1a1 1 0 011-1zm2.2 2.5L2.5 3.4c0 3.2 2.9 6.1 6.1 6.1l.9-.7-1.5-1.5-1 .6A5 5 0 014.1 5.1l.6-1z" fill-rule="evenodd"/></symbol>
  <symbol id="i-pin" viewBox="0 0 12 12"><path d="M6 0a4 4 0 014 4c0 3-4 8-4 8S2 7 2 4a4 4 0 014-4zm0 2.5a1.5 1.5 0 100 3 1.5 1.5 0 000-3z" fill-rule="evenodd"/></symbol>
  <symbol id="i-send" viewBox="0 0 12 12"><path d="M12 0L0 5.5l4.5 1.5L6 12zM4.5 7L11 1.5 5.6 8z"/></symbol>
  <symbol id="i-globe" viewBox="0 0 12 12"><path d="M6 0a6 6 0 110 12A6 6 0 016 0zM3 3c1 1 2 .5 2 2s-1.5 1-1.5 2.5S5 10 5 11c2-.5 1-2 2.5-3S10 7 10 5.5 8.5 4 8 3 7.5 1 6 1 4 2 3 3z" fill-rule="evenodd"/></symbol>
  <symbol id="i-pencil" viewBox="0 0 12 12"><path d="M9 0l3 3-7.5 7.5-3-3zM1 8.5l2.5 2.5L0 12z"/></symbol>
  <symbol id="i-info" viewBox="0 0 12 12"><path d="M6 0a6 6 0 110 12A6 6 0 016 0zM5.2 5v4.5h1.6V5zm.8-2.6a.9.9 0 100 1.8.9.9 0 000-1.8z" fill-rule="evenodd"/></symbol>
  <symbol id="i-clock" viewBox="0 0 12 12"><path d="M6 0a6 6 0 110 12A6 6 0 016 0zm0 1.6a4.4 4.4 0 100 8.8 4.4 4.4 0 000-8.8zM5.3 3h1.4v2.8l2 1.2-.7 1.2-2.7-1.6z" fill-rule="evenodd"/></symbol>
  <symbol id="i-plusbox" viewBox="0 0 12 12"><path d="M1 0h10a1 1 0 011 1v10a1 1 0 01-1 1H1a1 1 0 01-1-1V1a1 1 0 011-1zm4.2 3v2.2H3v1.6h2.2V9h1.6V6.8H9V5.2H6.8V3z" fill-rule="evenodd"/></symbol>
  <symbol id="i-download" viewBox="0 0 12 12"><path d="M5 0h2v5h2.5L6 8.5 2.5 5H5zM0 9h4.5L6 10.5 7.5 9H12v3H0z"/></symbol>
  <symbol id="i-xcircle" viewBox="0 0 12 12"><path d="M6 0a6 6 0 110 12A6 6 0 016 0zM3.9 2.8L2.8 3.9 4.9 6 2.8 8.1l1.1 1.1L6 7.1l2.1 2.1 1.1-1.1L7.1 6l2.1-2.1-1.1-1.1L6 4.9z" fill-rule="evenodd"/></symbol>
  <symbol id="i-swap" viewBox="0 0 12 12"><path d="M1 3h7V1l3 3-3 3V5H2.5v2H1zM11 9H4v2L1 8l3-3v2h5.5V5H11z"/></symbol>
  <symbol id="i-ban" viewBox="0 0 12 12"><path d="M6 0a6 6 0 110 12A6 6 0 016 0zm0 1.6c-.9 0-1.7.3-2.4.8l6 6A4.4 4.4 0 006 1.6zM2.4 3.6a4.4 4.4 0 006 6z" fill-rule="evenodd"/></symbol>
  <symbol id="i-smile" viewBox="0 0 12 12"><path d="M6 0a6 6 0 110 12A6 6 0 016 0zm0 1a5 5 0 100 10A5 5 0 006 1zM4 4a.8.8 0 110 1.6A.8.8 0 014 4zm4 0a.8.8 0 110 1.6A.8.8 0 018 4zM3.3 7h1a1.8 1.8 0 003.4 0h1a2.8 2.8 0 01-5.4 0z" fill-rule="evenodd"/></symbol>
  <symbol id="i-help" viewBox="0 0 12 12"><path d="M6 0a6 6 0 110 12A6 6 0 016 0zM5.2 8.3v1.5h1.6V8.3zM6 2.2c-1.4 0-2.4.8-2.5 2.1h1.5c.1-.5.4-.8 1-.8s.9.3.9.7c0 .9-1.7.9-1.7 2.7h1.5c0-1.2 1.8-1.2 1.8-2.8 0-1.1-1-1.9-2.5-1.9z" fill-rule="evenodd"/></symbol>
  <symbol id="i-inboxbox" viewBox="0 0 14 12"><path d="M2 0h10l2 6v6H0V6zM1.6 6h3l1 1.8h2.8l1-1.8h3L11 1.5H3z" fill-rule="evenodd"/></symbol>
  <symbol id="i-chev" viewBox="0 0 6 10"><path d="M1 0l5 5-5 5-1-1 4-4-4-4z"/></symbol>
  <symbol id="i-caret" viewBox="0 0 8 6"><path d="M0 1l1-1 3 3 3-3 1 1-4 4z"/></symbol>
</svg>

<header class="abs topbar">
  <div class="abs brand"><span class="brand-dot"></span>velorant</div>
  <div class="abs burger"><svg width="15" height="12"><rect width="15" height="2.4" fill="#fff"/><rect y="4.8" width="15" height="2.4" fill="#fff"/><rect y="9.6" width="15" height="2.4" fill="#fff"/></svg></div>
  <div class="abs top-item notify" style="left:911px"><svg class="ic" width="13" height="11"><use href="#i-inboxbox"/></svg><span class="count">4</span></div>
  <div class="abs top-item" style="left:959px"><svg class="ic" width="12" height="12"><use href="#i-tag"/></svg></div>
  <div class="abs top-item" style="left:989px"><span class="status-dot"></span>&nbsp;Available <svg class="ic" width="6" height="5"><use href="#i-caret"/></svg></div>
  <div class="abs top-item" style="left:1071px"><svg class="ic" width="10" height="10"><use href="#i-user"/></svg>&nbsp;Tomas Reyl <svg class="ic" width="6" height="5"><use href="#i-caret"/></svg></div>
  <div class="abs top-item" style="left:1160px"><svg class="ic" width="9" height="9"><use href="#i-help"/></svg></div>
</header>

<aside class="abs sidebar">
  <ul class="nav">
    <li><svg class="ic" width="9" height="9"><use href="#i-gauge"/></svg>DASHBOARD</li>
    <li class="active"><svg class="ic" width="9" height="9"><use href="#i-tray"/></svg>INBOX<span class="pill">4</span></li>
    <li><svg class="ic" width="9" height="9"><use href="#i-tag"/></svg>TICKETS</li>
    <li><svg class="ic" width="10" height="9"><use href="#i-users"/></svg>CLIENTS</li>
    <li><svg class="ic" width="9" height="9"><use href="#i-bars"/></svg>REPORTS</li>
    <li><svg class="ic" width="9" height="9"><use href="#i-gear"/></svg>SETTINGS<svg class="ic chev" width="4" height="7"><use href="#i-chev"/></svg></li>
  </ul>
</aside>
<div class="abs feedback"><svg class="ic" width="10" height="9"><use href="#i-mail"/></svg>Send Feedback</div>

<h1 class="abs page-title"><svg class="ic" width="13" height="11"><use href="#i-inboxbox"/></svg>Inbox</h1>
<div class="abs profile"><svg class="ic" width="10" height="10"><use href="#i-user"/></svg></div>

<nav class="abs tabs">
  <div class="tab active">Agent<sup>4</sup></div>
  <div class="tab dept">Department</div>
  <div class="tab acct">Account<sup>4</sup></div>
</nav>
<div class="abs panel"></div>

<div class="abs chat-list">
  <div class="chat active"><div class="av" role="img" aria-label="Customer profile photo"></div><div class="num">#4<br>Hello</div><div class="name">Nora Halvesen</div><div class="time"><svg class="ic" width="9" height="9"><use href="#i-chat"/></svg>21 days ago</div></div>
  <div class="chat"><div class="av"><svg class="ic" width="11" height="11"><use href="#i-user"/></svg></div><div class="num">#3<br>Hello</div><div class="name">Halvesen</div><div class="time"><svg class="ic" width="9" height="9"><use href="#i-chat"/></svg>21 days ago</div></div>
  <div class="chat"><div class="av"><svg class="ic" width="11" height="11"><use href="#i-user"/></svg></div><div class="num">#2<br>Hello</div><div class="name">Halvesen</div><div class="time"><svg class="ic" width="9" height="9"><use href="#i-chat"/></svg>21 days ago</div></div>
  <div class="chat"><div class="av"><svg class="ic" width="11" height="11"><use href="#i-user"/></svg></div><div class="num">#1<br>Hello</div><div class="name">Halvesen</div><div class="time"><svg class="ic" width="9" height="9"><use href="#i-chat"/></svg>21 days ago</div></div>
</div>
<div class="abs done"><b>DONE</b><span>No Done Clients</span></div>

<div class="abs conv-head"><span class="red-dot"></span>#4&nbsp; Nora Halvesen
  <div class="actions">
    <span class="btn close"><svg class="ic" width="8" height="8"><use href="#i-xcircle"/></svg>Close</span>
    <span class="btn transfer"><svg class="ic" width="9" height="8"><use href="#i-swap"/></svg>Transfer</span>
    <span class="btn ban"><svg class="ic" width="8" height="8"><use href="#i-ban"/></svg>Ban</span>
  </div>
</div>
<div class="abs orange-bar">
  <span><svg class="ic" width="8" height="8"><use href="#i-plusbox"/></svg>More Details</span>
  <span><svg class="ic" width="8" height="8"><use href="#i-download"/></svg>Save Transparent</span>
</div>
<div class="abs messages">
  <div class="abs msg-in"><div class="msg-av" role="img" aria-label="Customer profile photo"></div>Hello</div>
  <div class="abs msg-out"><div><b>Hi</b><em>21 days ago</em></div><div class="msg-av" role="img" aria-label="Agent profile photo"></div></div>
  <div class="abs composer">Type a message here <svg class="ic" width="10" height="10"><use href="#i-smile"/></svg></div>
</div>

<section class="abs details">
  <div class="dtabs">
    <div class="dtab active"><svg class="ic" width="9" height="9"><use href="#i-info"/></svg>Details</div>
    <div class="dtab"><svg class="ic" width="9" height="9"><use href="#i-tag"/></svg>Tickets</div>
    <div class="dtab"><svg class="ic" width="9" height="9"><use href="#i-clock"/></svg>History</div>
    <span class="minus"></span>
  </div>
  <div class="fields">
    <span class="f-name"><svg width="10" height="10"><path d="M0 0h10v2H6v6h2v2H2V8h2V2H0z" fill="currentColor"/></svg>Nora Halvesen</span>
    <span class="f-email"><svg class="ic" width="10" height="9"><use href="#i-mail"/></svg>Email</span>
    <span class="f-phone"><svg class="ic" width="9" height="9"><use href="#i-phone"/></svg>Phone</span>
    <span class="f-addr"><svg class="ic" width="9" height="10"><use href="#i-pin"/></svg>Address</span>
    <span class="f-city"><svg class="ic" width="10" height="10"><use href="#i-send"/></svg>City/Town</span>
    <span class="f-country"><svg class="ic" width="9" height="9"><use href="#i-globe"/></svg>Country</span>
    <span class="btn edit"><svg class="ic" width="8" height="8"><use href="#i-pencil"/></svg>Edit</span>
  </div>
</section>

<div class="abs footer-stats"><span>IP:</span><span>Country:</span><span>Pages:</span><span>Browser:</span><span>Devices:</span><span>OS:</span></div>
<div class="abs zoom">x10</div>

</body>
</html>
```